Elegant, Playful ReDesign of Paperlynx Website in wordpress - Budget has been raised

Project Brief: Paperlynx Website Redesign in WordPress

Introduction: Paperlynx, a cutting-edge document creation solution, aims to revolutionize the tedious process of crafting contracts, offers, forms, and other documents. By saving customers valuable time, streamlining workflows, and minimizing human error, Paperlynx has become an essential tool. As a technology company with a diverse clientele, we're set to boost our online presence through a refreshed WordPress website. Beyond a modernized website, we aspire to establish a stronger brand identity, incorporating graphic elements seamlessly into our online presence.

Current Status: Currently hosted on WordPress, Paperlynx's existing website serves its purpose but is ready for a visual transformation. Our goal is to maintain a modern and attractive appearance while upholding our commitment to simplicity and efficiency. Notably, the website is currently only in Danish. The redesigned structure should include a language switch function to cater to future international customers.

Objectives:
• Modern Aesthetic: Redesign the website with a fresh and modern vibe, reflecting innovation in the document creation sphere.
• User-Friendly: Prioritize an intuitive design for seamless navigation, ensuring visitors easily understand our offerings and benefits.
• Informative Content: Strike a balance between attractiveness and informativeness, clearly communicating Paperlynx's value proposition and simplifying business processes.
• Graphic Elements: Integrate visually appealing graphics that enhance the site's aesthetics and contribute to our overall visual identity. These elements should be versatile for future use in social media, advertisements, and other branding materials.
• Brand Recognition: Maintain our current logo and color scheme while exploring creative ways to establish a distinctive brand identity. The website should be a cornerstone for a cohesive branding strategy.
• Media Integration: Include images or videos on the website to enhance engagement. Find suitable, free-to-use visuals.
• Responsiveness: Ensure the design is responsive and works seamlessly on all devices.
• Demo Booking Form: Improve the design of the form to book a demo.
• Multilingual Support: Enable language transformation; the website is currently in Danish but should cater to other countries.

Guidelines:
• Typography: Up to the designer's discretion.
• Images/Videos: Must be free to use without additional charges.
• WordPress Theme: Use any WordPress theme below $100.
• Logo Redesign: Not needed; stick to the referenced color palette, as our new logo uses these colors.
• Color Palette: Stick to the existing company colors for consistency:
RGB
• #000b3c
• #004c6c
• #319ac3
• Greytones and white are also allowed
• Creativity Encouraged: Embrace creativity within the color palette for the layout, visuals, and overall user experience.

Conclusion: The Paperlynx website redesign marks an exciting opportunity to enhance our online presence. Our goal is to achieve a balance between a modern, attractive design and a clear, informative representation of our innovative solutions. We envision the revamped website as the foundation for a compelling online brand presence, with versatile graphic elements resonating across various digital platforms.

Sections that the website must include: Space for customer logos, space for testimonials, Space and redesign for display of price structure and price comparison, sections for company details and other information.

Design should also include a redesign of the customer cases section.
Generally there should just be a redesign of all things that are on the website.

Link to current website: https://paperlynx.example/

Target Market(s)

+50 employees.

Industry/Entity Type

Document automation

Coding

Coded - Design and coding required

Number of Pages Required

5+ page

Colors
0054AA
0677BA
7BADD7
CADEEF
E8F1F8

Requirements
Must have
• The new webpage must have the same pages as the current one. Frontpage, Book demo, About us, Case stories and Pricing

```html
<!DOCTYPE html>
<html lang="en">
<head>
<meta charset="utf-8">
<title>Paperlynx – Create contracts and quotes quickly</title>
<link href="https://fonts.googleapis.com/css2?family=Poppins:ital,wght@0,300;0,400;0,500;0,600;1,400&display=swap" rel="stylesheet">
<style>
:root{
  --blue:#1a8fca;
  --blue-deep:#0d86c2;
  --navy:#1b3a6b;
  --navy-dark:#14305c;
  --ink:#1d2a3a;
  --text:#555b66;
  --grey-bg:#f7f7f7;
  --line:#e6e8ec;
  --white:#ffffff;
  --gold:#f5b400;
}
*{margin:0;padding:0;box-sizing:border-box}
html,body{width:1200px;height:4796px;overflow:hidden}
body{font-family:"Poppins",sans-serif;color:var(--text);background:var(--white);position:relative}
.abs{position:absolute}
a{color:inherit;text-decoration:none}

/* header */
.site-header{position:absolute;left:0;top:0;width:1200px;height:100px;background:var(--white)}
.brand{position:absolute;left:89px;top:30px;display:flex;align-items:center;gap:10px}
.brand-mark{width:34px;height:34px;background:var(--blue)}
.brand-name{font-size:24px;font-weight:600;color:var(--navy);letter-spacing:.5px}
.main-nav{position:absolute;left:465px;top:42px;display:flex;gap:20px;font-size:13px;color:var(--ink)}
.main-nav a.active{color:var(--blue)}
.btn-demo{position:absolute;left:973px;top:32px;width:139px;height:39px;border-radius:20px;background:var(--blue);color:var(--white);font-size:13px;display:flex;align-items:center;justify-content:center}

/* hero */
.hero{position:absolute;left:0;top:100px;width:1200px;height:638px;background:linear-gradient(90deg,#9aa3ab 0%,#6f7d8c 30%,#2c4468 55%,#1d3a62 100%)}
.hero-title{position:absolute;left:599px;top:158px;width:540px;font-size:37px;line-height:50px;font-weight:400;color:var(--white)}
.hero-text{position:absolute;left:599px;top:302px;width:500px;font-size:14.5px;line-height:22px;color:var(--white)}
.btn-outline{position:absolute;border:1.5px solid var(--white);color:var(--white);font-size:13.5px;display:flex;align-items:center;justify-content:center}

/* benefit cards */
.benefit{position:absolute;top:738px;height:332px;background:var(--white);box-shadow:0 3px 8px rgba(0,0,0,.08);text-align:center}
.benefit.is-active{background:var(--navy)}
.icon-badge{position:absolute;left:50%;width:96px;height:96px;margin-left:-48px}
.benefit h3,.feature h3{position:absolute;left:0;width:100%;font-size:17px;font-weight:500;color:var(--navy);letter-spacing:.3px}
.benefit p,.feature p{position:absolute;left:50%;transform:translateX(-50%);font-size:12.5px;line-height:23px;color:var(--text)}
.is-active h3,.is-active p{color:var(--white)}

/* sections */
.section-title{position:absolute;left:0;width:1200px;text-align:center;font-size:40px;font-weight:400;color:var(--blue)}
.section-lead{position:absolute;left:50%;transform:translateX(-50%);text-align:center;font-size:14.5px;line-height:23px;color:var(--text)}
.demo{position:absolute;left:0;top:1125px;width:1200px;height:772px;background:var(--grey-bg)}
.video-frame{position:absolute;left:125px;top:173px;width:950px;height:508px;background:linear-gradient(100deg,#4e5763 0%,#6c6f73 40%,#8a8f96 60%,#3e4b5e 100%)}

.solution{position:absolute;left:0;top:1897px;width:1200px;height:787px;background:var(--white)}
.solution-photo{position:absolute;left:108px;top:67px;width:441px;height:657px;background:linear-gradient(160deg,#c9c1b5 0%,#ece6e0 45%,#3a4658 100%)}
.solution-title{position:absolute;left:605px;top:100px;font-size:40px;line-height:48px;color:var(--blue);font-weight:400}
.steps-line{position:absolute;left:617px;top:262px;width:2px;height:340px;background:#c9ced6}
.step{position:absolute;left:600px;width:480px}
.step-dot{position:absolute;left:0;top:0;width:34px;height:34px;border-radius:50%;border:2px solid #8fa4bf;background:var(--white)}
.step-dot::after{content:"";position:absolute;left:6px;top:6px;width:18px;height:18px;border-radius:50%;background:var(--navy)}
.step h4{position:absolute;left:52px;top:4px;font-size:21px;font-weight:400;font-style:italic;color:var(--blue);white-space:nowrap}
.step p{position:absolute;left:52px;top:44px;width:430px;font-size:14px;line-height:25px;color:var(--text)}

.mobile-band{position:absolute;left:0;top:2684px;width:1200px;height:374px;background:linear-gradient(90deg,#2d4a74 0%,#213f6c 50%,#2a4a77 100%)}
.mobile-title{position:absolute;left:0;top:84px;width:1200px;text-align:center;font-size:39px;color:var(--white);font-weight:400}
.mobile-text{position:absolute;left:120px;top:150px;width:960px;text-align:center;font-size:14.5px;line-height:25px;color:var(--white)}

.features{position:absolute;left:0;top:3058px;width:1200px;height:634px;background:var(--white)}
.feature{position:absolute;top:227px;height:318px;background:var(--grey-bg);box-shadow:0 2px 8px rgba(0,0,0,.08);text-align:center}
.feature.is-active{background:linear-gradient(160deg,#2b2a2a 0%,#4a3a2e 50%,#1e1d1d 100%);border-radius:4px}

.testimonials{position:absolute;left:0;top:3692px;width:1200px;height:525px;background:var(--grey-bg)}
.quote-card{position:absolute;top:149px;width:324px;height:279px;background:var(--white);box-shadow:0 2px 10px rgba(0,0,0,.07)}
.avatar{position:absolute;left:34px;top:40px;width:84px;height:84px;border-radius:50%;background:linear-gradient(160deg,#9fb6c9,#5f7a92)}
.quote-name{position:absolute;left:134px;top:58px;font-size:14.5px;font-weight:600;color:var(--ink)}
.quote-place{position:absolute;left:134px;top:78px;font-size:12.5px;color:var(--text)}
.stars{position:absolute;left:134px;top:94px;font-size:12px;color:var(--gold);letter-spacing:1px}
.quote-text{position:absolute;left:24px;top:160px;width:280px;font-size:15px;line-height:26px;color:var(--ink)}

.site-footer{position:absolute;left:0;top:4217px;width:1200px;height:470px;background:var(--blue-deep)}
.footer-col{position:absolute;top:120px;color:var(--white)}
.footer-col h5{font-size:19px;font-weight:400}
.footer-col h5 b{font-weight:600}
.footer-col h5::after{content:"";display:block;width:40px;height:2px;background:var(--white);margin-top:12px}
.footer-links{list-style:none;margin-top:38px;font-size:14.5px}
.footer-links li{height:31px;padding-left:24px;position:relative}
.footer-links li::before{content:"";position:absolute;left:6px;top:7px;width:6px;height:6px;border-right:1.5px solid #fff;border-top:1.5px solid #fff;transform:rotate(45deg)}
.newsletter-text{margin-top:38px;width:260px;font-size:14.5px;line-height:20px}
.newsletter-input{margin-top:20px;width:249px;height:38px;background:var(--white);border:none}
.newsletter-btn{margin-top:14px;width:125px;height:36px;background:var(--white);color:var(--navy);font-size:13px;display:flex;align-items:center;justify-content:center}

.bottom-bar{position:absolute;left:0;top:4687px;width:1200px;height:109px;background:var(--navy-dark)}
.copyright{position:absolute;left:89px;top:42px;font-size:17px;color:var(--white)}
.social{position:absolute;top:33px;width:42px;height:42px;border-radius:50%;border:2px solid var(--white)}
</style>
</head>
<body>

<header class="site-header">
  <div class="brand"><span class="brand-mark"></span><span class="brand-name">PAPERLYNX</span></div>
  <nav class="main-nav">
    <a class="active">FRONT PAGE</a><a>KUNDECASES</a><a>VIDEO</a><a>LIVE DEMO</a><a>PRICES</a><a>ABOUT US</a>
  </nav>
  <a class="btn-demo">BOOK DEMO</a>
</header>

<section class="hero">
  <div class="abs" role="img" aria-label="Woman reviewing contract papers at a desk" style="left:0;top:0;width:1200px;height:638px"></div>
  <h1 class="hero-title">CREATE CONTRACTS AND QUOTES QUICKLY</h1>
  <p class="hero-text">Lorem ipsum dolor sit amet, consectetur adipiscing elit, sed do eiusmod tempor incididunt ut labore et dolore magna aliqua. Quis ipsum suspendisse ultrices gravida.</p>
  <a class="btn-outline" style="left:599px;top:430px;width:155px;height:41px">READ MORE</a>
</section>

<svg width="0" height="0" style="position:absolute">
  <defs>
    <g id="badge">
      <circle cx="48" cy="48" r="46" fill="none" stroke="#1a8fca" stroke-width="2" stroke-dasharray="2 3"/>
      <circle cx="48" cy="48" r="38" fill="#1a8fca"/>
    </g>
    <g id="badge-light">
      <circle cx="48" cy="48" r="46" fill="none" stroke="#ffffff" stroke-width="2" stroke-dasharray="2 3"/>
      <circle cx="48" cy="48" r="38" fill="#1a8fca"/>
    </g>
  </defs>
</svg>

<article class="benefit" style="left:87px;width:339px">
  <svg class="icon-badge" style="top:40px" viewBox="0 0 96 96"><use href="#badge"/>
    <path d="M34 38h8l6 16h16M40 58h28M44 46h18" stroke="#fff" stroke-width="3" fill="none" stroke-linecap="round"/></svg>
  <h3 style="top:162px">SAVE TIME</h3>
  <p style="top:192px;width:250px">Reduce your time spent by as much as 90% when creating customer contracts and quotes.</p>
</article>
<article class="benefit is-active" style="left:428px;width:344px">
  <svg class="icon-badge" style="top:40px" viewBox="0 0 96 96"><use href="#badge-light"/>
    <path d="M48 30v36M32 39l32 18M32 57l32-18" stroke="#fff" stroke-width="3" stroke-linecap="round"/><circle cx="48" cy="48" r="6" fill="#fff"/></svg>
  <h3 style="top:162px">HIGH QUALITY</h3>
  <p style="top:192px;width:270px">Automation gives you minimal work and eliminates errors in your documents.</p>
  <svg class="abs" style="left:164px;top:283px" width="18" height="18" viewBox="0 0 18 18"><circle cx="9" cy="9" r="7.5" fill="none" stroke="#1a8fca" stroke-width="1.5"/><path d="M6 9h6M9.5 6.5 12 9l-2.5 2.5" stroke="#1a8fca" stroke-width="1.5" fill="none"/></svg>
</article>
<article class="benefit" style="left:772px;width:340px">
  <svg class="icon-badge" style="top:40px" viewBox="0 0 96 96"><use href="#badge"/>
    <circle cx="48" cy="48" r="11" fill="none" stroke="#fff" stroke-width="6" stroke-dasharray="4 3"/><circle cx="48" cy="48" r="5" fill="#fff"/></svg>
  <h3 style="top:162px">STREAMLINED FLOW</h3>
  <p style="top:192px;width:280px">Be guided all the way through the document and ask for review before sending the document for digital signature.</p>
</article>

<section class="demo">
  <h2 class="section-title" style="top:30px">START LIVE DEMO</h2>
  <p class="section-lead" style="top:88px;width:820px">Experience the intuitive and intelligent flow for creating documents on your own. In minutes, you'll have a complete document – ready for digital signature.</p>
  <div class="video-frame" role="img" aria-label="Video still of two colleagues working on documents at a table"></div>
  <svg class="abs" style="left:566px;top:394px" width="68" height="68" viewBox="0 0 68 68">
    <circle cx="34" cy="34" r="32" fill="#fff" fill-opacity=".9" stroke="#1a8fca" stroke-width="2"/>
    <circle cx="34" cy="34" r="25" fill="#fff"/>
    <path d="M27 21v26l21-13z" fill="#1a8fca"/>
  </svg>
</section>

<section class="solution">
  <div class="solution-photo" role="img" aria-label="Woman reading a document at home"></div>
  <h2 class="solution-title">INTELLIGENT DOKUMENT<br>LØSNING</h2>
  <div class="steps-line"></div>
  <div class="step" style="top:242px"><span class="step-dot"></span><h4>1. Select document</h4><p>Fill out our simple online form with your relevant details. tailor our services to your specific situation.</p></div>
  <div class="step" style="top:423px"><span class="step-dot"></span><h4>2. Udfyld guided flow</h4><p>Our experienced team will assess your eligibility for opportunities for refunds</p></div>
  <div class="step" style="top:585px"><span class="step-dot"></span><h4>3. Sign digitally</h4><p>Once we've gathered the necessary information, we'll ensuring accuracy and efficiency.</p></div>
</section>

<section class="mobile-band" role="img" aria-label="Team meeting with a client, blue toned">
  <h2 class="mobile-title">AKTIVÉR FROM MOBILE</h2>
  <p class="mobile-text">Create your documents at your convenience. They can be created on any device and signed much faster.create an offer on a mobile or tablet while talking to a potential customer in a meeting. Get acceptance right away and send it for digital signature before you go home.</p>
  <a class="btn-outline" style="left:523px;top:255px;width:154px;height:38px">GET STARTED</a>
</section>

<section class="features">
  <h2 class="section-title" style="top:80px">LOTS OF FEATURES</h2>
  <p class="section-lead" style="top:138px;width:820px">Experience the intuitive and intelligent flow for creating documents on your own. In minutes, you'll have a complete document – ready for digital signature.</p>

  <article class="feature" style="left:91px;width:335px">
    <svg class="icon-badge" style="top:24px" viewBox="0 0 96 96"><use href="#badge"/>
      <path d="M48 30l14 5v12c0 10-7 16-14 19-7-3-14-9-14-19V35z" fill="none" stroke="#fff" stroke-width="3"/><path d="M48 40l3 6 6 1-4.5 4 1 6-5.5-3-5.5 3 1-6-4.5-4 6-1z" fill="#fff"/></svg>
    <h3 style="top:146px">DIGITAL SIGNATURE</h3>
    <p style="top:178px;width:290px">Send your offers for digital signature with data directly from your CRM solution – quickly and easily.</p>
  </article>
  <article class="feature is-active" style="left:431px;width:333px" role="img" aria-label="Dark photo of a person using a laptop">
    <svg class="icon-badge" style="top:24px" viewBox="0 0 96 96">
      <circle cx="48" cy="48" r="46" fill="none" stroke="#fff" stroke-width="2" stroke-dasharray="2 3"/><circle cx="48" cy="48" r="38" fill="#fff"/>
      <ellipse cx="48" cy="48" rx="18" ry="7" fill="none" stroke="#1a8fca" stroke-width="2.5"/><ellipse cx="48" cy="48" rx="18" ry="7" fill="none" stroke="#1a8fca" stroke-width="2.5" transform="rotate(60 48 48)"/><ellipse cx="48" cy="48" rx="18" ry="7" fill="none" stroke="#1a8fca" stroke-width="2.5" transform="rotate(-60 48 48)"/><circle cx="48" cy="48" r="3.5" fill="#1a8fca"/></svg>
    <h3 style="top:146px">AUTOMATED OFFERS</h3>
    <p style="top:176px;width:280px">Create error-free offers with data from your CRM solution using a guided flow and avoid manual errors.</p>
    <svg class="abs" style="left:157px;top:277px" width="18" height="18" viewBox="0 0 18 18"><circle cx="9" cy="9" r="7.5" fill="none" stroke="#1a8fca" stroke-width="1.5"/><path d="M6 9h6M9.5 6.5 12 9l-2.5 2.5" stroke="#1a8fca" stroke-width="1.5" fill="none"/></svg>
  </article>
  <article class="feature" style="left:774px;width:334px">
    <svg class="icon-badge" style="top:24px" viewBox="0 0 96 96"><use href="#badge"/>
      <circle cx="42" cy="53" r="10" fill="none" stroke="#fff" stroke-width="6" stroke-dasharray="4 3"/><circle cx="58" cy="40" r="7" fill="none" stroke="#fff" stroke-width="5" stroke-dasharray="3 2.5"/></svg>
    <h3 style="top:146px">LEADS FRA DIT WEBSITE</h3>
    <p style="top:178px;width:290px">Give your lead an estimate price or quote draft right away, which you can work on from your CRM solution</p>
  </article>
</section>

<section class="testimonials">
  <h2 class="section-title" style="top:64px">CLIENTS TESTIMONIALS</h2>
  <article class="quote-card" style="left:99px">
    <div class="avatar" role="img" aria-label="Client portrait"></div>
    <div class="quote-name">Nora K</div><div class="quote-place">Lakeview, MD</div><div class="stars">★★★★★</div>
    <p class="quote-text">My mom is in an assisted living facility and has Alzheimers. We portrait made into contracts .</p>
  </article>
  <article class="quote-card" style="left:439px">
    <div class="avatar" role="img" aria-label="Client portrait"></div>
    <div class="quote-name">Nora K</div><div class="quote-place">Lakeview, MD</div><div class="stars">★★★★★</div>
    <p class="quote-text">My mom is in an assisted living facility and has Alzheimers. We portrait made into contracts .</p>
  </article>
  <article class="quote-card" style="left:779px">
    <div class="avatar" role="img" aria-label="Client portrait"></div>
    <div class="quote-name">Nora K</div><div class="quote-place">Lakeview, MD</div><div class="stars">★★★★★</div>
    <p class="quote-text">My mom is in an assisted living facility and has Alzheimers. We portrait made into contracts .</p>
  </article>
</section>

<footer class="site-footer">
  <div class="footer-col" style="left:242px">
    <h5>Quick <b>Links</b></h5>
    <ul class="footer-links"><li>Home</li><li>About Us</li><li>Live Demo</li><li>Lot Of Features</li><li>Testimonials</li></ul>
  </div>
  <div class="footer-col" style="left:498px">
    <h5>Quick <b>Links</b></h5>
    <ul class="footer-links"><li>Terms &amp; Condition</li><li>Privacy Policy</li><li>Support</li></ul>
  </div>
  <div class="footer-col" style="left:757px">
    <h5>Our <b>Newsletter</b></h5>
    <p class="newsletter-text">Subscribe our newsletter to get the latest news.</p>
    <div class="newsletter-input"></div>
    <div class="newsletter-btn">SUBSCRIBE</div>
  </div>
</footer>

<div class="bottom-bar">
  <p class="copyright">All Rights Reserved @ Copyrights 2023</p>
  <span class="social" style="left:913px" aria-label="Video channel"></span>
  <span class="social" style="left:965px" aria-label="Social profile"></span>
  <span class="social" style="left:1017px" aria-label="Social profile"></span>
  <span class="social" style="left:1069px" aria-label="Photo profile"></span>
</div>

</body>
</html>
```